A5 Patient Information Booklet (Chiropractic Clinic) 4-8 pages

Here’s a polished, professional rewrite of your full brief and content, with clearer structure, corrected language, and a premium tone:

---

**Project Title:** Premium Patient Information Brochure (Chiropractic & Wellness Clinic)

---

### **Overview**

We are a health and wellness clinic seeking a premium, high-end patient information brochure to provide following a patient’s initial consultation and first treatment.

The purpose of this booklet is to:

* Reinforce trust and professionalism
* Help patients understand what to expect next
* Encourage adherence to care recommendations
* Position the clinic as calm, expert-led, and results-driven

---

### **Format**

* 4–8 page booklet (A5 or similar size)
* Print-ready and digital versions required

---

### **Target Audience**

Patients who have just completed their initial consultation and may have begun treatment. They may already be experiencing physical or mental changes, so the brochure should guide, reassure, and educate them on what comes next.

---

### **Tone & Style**

* Premium, calm, and reassuring
* Modern wellness aesthetic (not overly clinical)
* Clean layout with minimal clutter
* Soft, neutral colour palette (whites, creams, muted greens, soft blues)
* Elegant typography (e.g. Montserrat / Lato)
* High-end, trustworthy, and professional feel

---

### **Key Messages**

#### 1. Listen to Your Body

Patients may feel different after treatment. Reassure them that this is normal and part of the healing process.

#### 2. Post-Treatment Advice

* Stay well hydrated
* Rest if needed
* Avoid overexertion if the body requires recovery

#### 3. Healing is a Journey (Core Concept)

A strong visual metaphor of a **“road to recovery”** or **journey** should be central to the design.

This journey should clearly illustrate three phases:

* **Phase 1: Initial Care (Weeks 1–6)**
Focus: Reducing pain/discomfort, calming the body, and initiating response to treatment

* **Phase 2: Corrective Care (Weeks 6–12)**
Focus: Addressing underlying issues, improving function, and creating lasting change

* **Phase 3: Wellness / Maintenance (Ongoing)**
Focus: Maintaining progress, preventing relapse, and supporting long-term wellbeing

**Important:**

* Emphasise that this is not a quick fix
* Progress requires time and consistency
* Each patient follows an individualised care plan
* The journey should feel structured, positive, and achievable

#### 4. Personalised Care

Reinforce that every treatment plan is tailored specifically to the individual.

#### 5. Professional Reassurance

Patients should feel confident they are in expert hands and supported throughout their journey.

---

### **Design Direction**

* Use imagery that reflects calmness, progression, and wellness (e.g. pathways, nature, soft gradients)
* Avoid generic stock imagery
* **Only use original clinic images from website and social media**
* Prioritise white space and clarity
* Aim for a luxury spa/medical hybrid aesthetic

---

## **Content Structure (Page-by-Page)**

### **Front Cover**

* Clean, minimal, premium design
* Clinic branding

---

### **Page 1: Patient Case Summary**

**Title:** *Welcome to Fernwell Spine Studio*

Thank you for choosing Fernwell Spine Studio.

This booklet is designed to guide you through:

* What we found during your initial consultation
* Your personalised recommended treatment plan
* Your road to recovery
* Long-term wellness care
* Why we take the approach we do

---

### **Page 2: Your Care Journey**

**Stage 1: Your Initial Consultation**

Today we completed a comprehensive assessment of your health and function, including:

* Full case history and discussion of your symptoms and goals
* Orthopaedic and neurological testing
* Postural and movement assessment
* Initial treatment (where appropriate)

**What this tells us:**

* How your body is currently functioning
* Where areas of stress or dysfunction may be present
* The most appropriate and effective path forward for your care

---

### **Page 3: Your Suggested Treatment Plan**

Based on today’s findings, your recommended care plan is:

**______ treatments over ______ weeks**

This should be viewed alongside your *Road to Recovery* to help you understand what to expect.

We have also discussed:

* Expected timelines for improvement
* Available payment options

**After Treatment:**
It is common to feel different following treatment. This is a normal response as your body begins to adapt and respond.

We recommend:

* Staying well hydrated
* Allowing time for rest and recovery
* Avoiding overexertion if your body feels it needs it

---

### **Page 4: What to Expect Next**

Healing is not always linear—it is a process that occurs over time.

Your care will typically progress through the following stages:

* **Relief Care**
Focused on reducing discomfort and calming the body

* **Corrective Care**
Focused on addressing underlying issues and improving function
(This phase may include prescribed exercises)

* **Maintenance / Wellness Care**
Focused on sustaining progress, preventing recurrence, and supporting long-term health

---

### **Page 5: Understanding Chiropractic Care**

**What is Chiropractic?**
Chiropractic care focuses on the relationship between the spine, nervous system, and overall body function.

By improving spinal movement and alignment, chiropractic care helps support the nervous system, allowing the body to function and heal more effectively.

**About Fernwell Spine Studio**
At Fernwell Spine Studio, our approach is centred around personalised, patient-focused care. We aim to not only relieve symptoms but to address underlying causes and support long-term wellbeing.

---

### **Back Page**

* Clinic contact details
* Website
* Social media icons/handles

**Closing Message:**
“A healthier, stronger you—supported every step of the way.”

---

### **Deliverables**

* Print-ready PDF
* Editable source files

---

### **Additional Notes**

* The brochure should feel valuable and worth keeping
* Encourage long-term care in a subtle, non-pushy way
* Maintain clarity, readability, and strong visual hierarchy
* Balance professionalism with warmth and approachability

---

If you’d like, I can also turn this into **actual brochure copy (fully written, patient-facing text)** or help you refine it further for a designer.

Existing patients who want to feel better and look after themselves that is given after their initil consultation appointment

Chiropractic, wellness, health

• Montserrat or Lato

0094D4
00A9DD
6FCCEA
C7EBF8
E9F6FB
00AB8E
00BBA5
67D7C9
C6EFE9
E9F9F6
6B429C
8869AF
B7A5CE
E3DAEB
F3F0F8

• my own photos, look premium wellness, be clear and simple to understand for patients journey or what to expect next and over time
• USe my social media/website for ideas
• generic photos and images

```html
<!DOCTYPE html>
<html lang="en">
<head>
<meta charset="utf-8">
<title>Fernwell Spine Studio – Patient Booklet</title>
<link href="https://fonts.googleapis.com/css2?family=Montserrat:wght@400;600;700;800&family=Lato:wght@400;700&display=swap" rel="stylesheet">
<style>
:root{
  --teal:#00AB8E;
  --teal-bright:#00BBA5;
  --teal-soft:#C6EFE9;
  --teal-mist:#E9F9F6;
  --blue:#0094D4;
  --blue-soft:#6FCCEA;
  --blue-mist:#E9F6FB;
  --purple:#6B429C;
  --violet:#8869AF;
  --pink:#CF73B8;
  --sky:#7DA9E0;
  --pin:#B52FB0;
  --ink:#1F1F24;
  --grey:#5E6470;
  --backdrop:#9B9B9B;
  --panel:linear-gradient(100deg,var(--pink) 0%,var(--violet) 45%,var(--sky) 100%);
  --heading:'Montserrat',sans-serif;
  --body:'Lato',sans-serif;
}
*{margin:0;padding:0;box-sizing:border-box}
html,body{width:1200px;height:3335px;overflow:hidden}
body{background:var(--backdrop);font-family:var(--body);color:var(--ink);position:relative}
.spread{position:absolute;left:50px;width:1100px;height:775px;background:#fff;overflow:hidden;box-shadow:0 6px 18px rgba(0,0,0,.25)}
.spread--cover{top:252px;background:linear-gradient(160deg,#DDF3F6 0%,#F7FCFD 45%,#E3F5F7 100%)}
.spread--inside-a{top:1279px}
.spread--inside-b{top:2306px}
.abs{position:absolute}

/* brand lockup */
.brand{position:absolute;display:flex;flex-direction:column;align-items:center;text-align:center}
.brand__dot{width:var(--d,56px);height:var(--d,56px);border-radius:50%;border:3px solid var(--teal);margin-bottom:8px}
.brand__name{font-family:var(--heading);font-weight:700;color:var(--ink);letter-spacing:.5px;line-height:1.15}

/* cover */
.cover__ghost{left:80px;top:108px;width:388px;height:388px;border-radius:50%;border:10px solid rgba(200,210,214,.28)}
.book{left:253px;top:603px;font-size:13px;color:var(--ink)}
.book__title{font-family:var(--heading);font-weight:800;font-size:15px;margin-bottom:12px}
.book__title span{color:var(--pink)}
.book__row{display:flex;gap:9px;align-items:flex-start;margin-bottom:10px;line-height:1.25}
.book__row svg{flex:none;margin-top:2px}
.cover__photo{left:675px;top:194px;width:302px;height:302px;border-radius:50%;padding:10px;background:linear-gradient(135deg,var(--pink),var(--violet),var(--sky))}
.cover__photo div{width:100%;height:100%;border-radius:50%;background:radial-gradient(circle at 45% 40%,#E7D9CC 0%,#B9A08A 45%,#59626F 100%)}
.cover__kicker{left:620px;top:515px;width:412px;display:flex;align-items:center;gap:10px;font-family:var(--heading);font-size:23px;letter-spacing:3px;color:var(--ink)}
.cover__kicker::before,.cover__kicker::after{content:"";flex:1;height:1px;background:var(--ink)}
.cover__title{left:600px;top:545px;width:452px;text-align:center;font-family:var(--heading);font-weight:800;font-size:41px;line-height:1;color:var(--teal)}
.cover__intro{left:615px;top:632px;width:422px;text-align:center;font-size:10.5px;line-height:1.3;color:var(--ink)}
.pill-url{position:absolute;border-radius:20px;background:var(--panel);color:#fff;font-family:var(--heading);font-weight:700;text-align:center}
.cover__url{left:686px;top:700px;width:280px;height:28px;line-height:28px;font-size:15px}

/* inside common */
.section-icon{width:40px;height:40px;border-radius:50%;border:2px solid var(--teal);display:flex;align-items:center;justify-content:center}
.h-section{font-family:var(--heading);font-weight:800;line-height:1.1;text-transform:uppercase}
.h-section .accent{color:var(--teal)}
.gradient-panel{background:var(--panel);border-radius:14px;color:#fff}
.photo{background:linear-gradient(150deg,#E8DCD2,#B49C89 55%,#5A6472)}
.footer-dot{width:34px;height:34px;border-radius:50%;border:2px solid var(--teal)}
.footer-rule{height:1px;background:#C9CDD2}
.footer-url{height:16px;line-height:16px;font-size:9.5px;font-weight:600}
.page-no{font-family:var(--heading);font-weight:700;font-size:10px}
.ticks{list-style:none}
.ticks li{position:relative;padding-left:18px}
.ticks li::before{content:"";position:absolute;left:0;top:4px;width:9px;height:9px;border-radius:50%;border:2px solid currentColor;opacity:.8}

/* first appointment */
.first__photo{left:10px;top:110px;width:240px;height:315px;border-radius:12px 0 0 12px}
.first__panel{left:241px;top:116px;width:261px;height:309px;padding:22px 20px 0 20px;font-size:12.5px;line-height:1.3}
.first__panel h3{font-family:var(--heading);font-size:15px;font-weight:600;text-transform:uppercase;line-height:1.15;margin-bottom:10px}
.first__panel .lead{font-size:15px;margin-bottom:12px}
.first__panel .ticks li{margin-bottom:10px}
.first__panel .ticks li::before{border-color:#fff}
.told{left:49px;top:466px;font-size:14px}
.told h4{font-size:15px;font-weight:400;margin-bottom:16px}
.told .ticks li{margin-bottom:14px;font-size:13px}
.told .ticks li::before{border-color:var(--teal)}
.told__note{left:49px;top:602px;width:212px;height:61px;background:var(--teal);color:#fff;border-radius:0 0 0 12px;font-size:13px;line-height:1.25;padding:14px 16px}
.told__photo{left:259px;top:463px;width:243px;height:200px;border-radius:12px}

/* journey */
.road{left:515px;top:200px;width:585px;height:575px;background:
  radial-gradient(ellipse 70% 60% at 38% 78%,#8F9297 0%,#B9BCC0 38%,rgba(225,227,229,.55) 62%,rgba(255,255,255,0) 80%)}
.phase-label{font-family:var(--heading);font-weight:700;font-size:15px;color:var(--sky)}
.phase-pill{height:20px;display:flex;align-items:center;justify-content:space-between;padding:0 4px 0 12px;border-radius:12px;background:var(--panel);font-family:var(--heading);font-weight:700;font-size:9px;color:#fff}
.phase-pill b{background:#fff;color:var(--ink);border-radius:10px;padding:2px 8px;font-size:8.5px}
.phase-focus{font-size:12.5px;line-height:1.2;color:var(--ink)}

/* listen + advice */
.listen{left:56px;top:58px;width:185px}
.listen p,.advice li{font-size:12.5px;line-height:1.25;margin-top:10px}
.split{left:255px;top:54px;width:1px;height:118px;background:#C9CDD2}
.advice{left:287px;top:58px;width:230px}
.advice .ticks li{margin-top:6px}
.advice .ticks li::before{border-color:var(--pink);background:var(--pink)}
.care__photo{left:0;top:204px;width:313px;height:571px;border-radius:0 60px 0 0}
.care__panel{left:292px;top:222px;width:210px;height:390px;padding:38px 18px 0 50px;border-radius:16px 16px 16px 0}
.care__panel h3{font-family:var(--heading);font-weight:800;font-size:15px;line-height:1.15;margin-bottom:14px}
.care__panel p{font-size:12.5px;line-height:1.3;margin-bottom:50px}

/* care plan pad */
.pad{left:600px;top:65px;width:448px;height:599px;border-radius:10px;background:linear-gradient(90deg,var(--pink),var(--violet),var(--sky));padding-top:36px}
.pad__spiral{position:absolute;left:12px;right:12px;top:8px;height:14px;border-top:4px dotted #3A3D44;border-bottom:2px solid #3A3D44}
.pad__sheet{position:absolute;left:19px;top:38px;width:412px;height:539px;background:#fff;border-radius:14px}
.pad-tag{position:absolute;left:20px;height:16px;line-height:16px;padding:0 12px;border-radius:8px;background:var(--teal);color:#fff;font-family:var(--heading);font-weight:700;font-size:9.5px}
.pad-line{position:absolute;left:20px;width:375px;height:17px;border-radius:8px;background:var(--teal-mist);border:1px solid var(--teal-soft)}
.pad-weeks{position:absolute;right:17px;height:17px;line-height:17px;padding:0 14px;border-radius:8px;background:var(--pink);color:#fff;font-family:var(--heading);font-weight:700;font-size:9px}
</style>
</head>
<body>

<section class="spread spread--cover" aria-label="Front and back cover">
  <div class="abs cover__ghost" aria-hidden="true"></div>

  <div class="brand" style="left:50px;top:603px;width:175px;--d:64px">
    <div class="brand__dot"></div>
    <div class="brand__name" style="font-size:15px">FERNWELL SPINE STUDIO</div>
  </div>

  <div class="abs book">
    <div class="book__title">BOOK AN <span>APPOINTMENT</span></div>
    <div class="book__row">
      <svg width="11" height="14" viewBox="0 0 24 30"><path d="M12 0C5.4 0 0 5.3 0 11.8 0 20.6 12 30 12 30s12-9.4 12-18.2C24 5.3 18.6 0 12 0zm0 16a4.5 4.5 0 110-9 4.5 4.5 0 010 9z" fill="var(--teal)"/></svg>
      <span>Fernwell Spine Studio<br>14 Elm Row,<br>Dunmere DN4 7QT</span>
    </div>
    <div class="book__row">
      <svg width="12" height="10" viewBox="0 0 24 18"><rect x="1" y="1" width="22" height="16" rx="2" fill="none" stroke="var(--teal)" stroke-width="2.5"/><path d="M2 2l10 8 10-8" fill="none" stroke="var(--teal)" stroke-width="2.5"/></svg>
      <span>info@fernwellspine.com</span>
    </div>
    <div class="book__row">
      <svg width="12" height="12" viewBox="0 0 24 24"><circle cx="12" cy="12" r="10.5" fill="none" stroke="var(--teal)" stroke-width="2"/><path d="M1.5 12h21M12 1.5c4 4 4 17 0 21M12 1.5c-4 4-4 17 0 21" fill="none" stroke="var(--teal)" stroke-width="1.8"/></svg>
      <span>www.fernwellspine.com</span>
    </div>
  </div>

  <div class="brand" style="left:735px;top:34px;width:185px;--d:70px">
    <div class="brand__dot"></div>
    <div class="brand__name" style="font-size:17px">FERNWELL SPINE STUDIO</div>
  </div>

  <div class="abs cover__photo"><div role="img" aria-label="Chiropractor gently assessing a seated patient's back in the clinic"></div></div>

  <div class="abs cover__kicker">LOOKING FOR A</div>
  <h1 class="abs cover__title">CHIROPRACTOR<br>IN DUNMERE?</h1>
  <p class="abs cover__intro">Fernwell Spine Studio provides gentle chiropractic care in the centre of Dunmere, helping people with back pain, neck tension, headaches and sports injuries. If you're considering chiropractic care but aren't quite sure what to expect, you're not alone. This page is here to answer common questions and help you feel confident about your first visit.</p>
  <div class="pill-url cover__url">www.fernwellspine.com</div>
</section>

<section class="spread spread--inside-a" aria-label="Pages one and two">
  <div class="abs section-icon" style="left:52px;top:44px">
    <svg width="20" height="20" viewBox="0 0 24 24"><rect x="3" y="4" width="18" height="17" rx="2" fill="none" stroke="var(--ink)" stroke-width="2"/><path d="M3 9h18M8 2v4M16 2v4" stroke="var(--ink)" stroke-width="2"/></svg>
  </div>
  <h2 class="abs h-section" style="left:105px;top:44px;font-size:20px"><span class="accent">What happens at your first</span><br>appointment?</h2>

  <div class="abs photo first__photo" role="img" aria-label="Chiropractor assessing a patient lying on the treatment table"></div>
  <div class="abs gradient-panel first__panel">
    <h3>Your first visit is about understanding you</h3>
    <p class="lead">We'll begin with a<br>conversation about</p>
    <ul class="ticks">
      <li>Your health history</li>
      <li>Any concerns you have</li>
      <li>How you'd like to feel and function</li>
    </ul>
    <p>This is followed by a physical assessment to look at posture, movement, and how your body is working as a whole.</p>
  </div>

  <div class="abs told">
    <h4>You'll always be told</h4>
    <ul class="ticks">
      <li>What we find</li>
      <li>What it means for you</li>
      <li>What your options are</li>
    </ul>
  </div>
  <div class="abs told__note">Care is gentle, appropriate, and tailored to your needs.</div>
  <div class="abs photo told__photo" role="img" aria-label="Chiropractor examining a patient's upper back"></div>

  <div class="abs footer-dot" style="left:52px;top:702px"></div>
  <div class="abs footer-rule" style="left:92px;top:725px;width:212px"></div>
  <div class="pill-url footer-url" style="left:302px;top:717px;width:182px">www.fernwellspine.com</div>
  <div class="abs page-no" style="left:492px;top:718px">01</div>

  <div class="abs road" role="img" aria-label="Winding road to recovery running through the three care phases"></div>

  <div class="abs section-icon" style="left:557px;top:41px;width:56px;height:56px">
    <svg width="28" height="28" viewBox="0 0 24 24"><circle cx="6" cy="6" r="3" fill="none" stroke="var(--ink)" stroke-width="2"/><circle cx="18" cy="18" r="3" fill="none" stroke="var(--ink)" stroke-width="2"/><path d="M9 6h7a3 3 0 010 6H8a3 3 0 000 6h7" fill="none" stroke="var(--ink)" stroke-width="2"/></svg>
  </div>
  <h2 class="abs h-section" style="left:627px;top:43px;font-size:32px"><span class="accent">Your recovery</span><br>journey</h2>

  <svg class="abs" style="left:638px;top:176px" width="40" height="60" viewBox="0 0 24 30"><path d="M12 0C5.4 0 0 5.3 0 11.8 0 20.6 12 30 12 30s12-9.4 12-18.2C24 5.3 18.6 0 12 0zm0 16a4.5 4.5 0 110-9 4.5 4.5 0 010 9z" fill="var(--pin)"/></svg>
  <svg class="abs" style="left:700px;top:285px" width="46" height="67" viewBox="0 0 24 30"><path d="M12 0C5.4 0 0 5.3 0 11.8 0 20.6 12 30 12 30s12-9.4 12-18.2C24 5.3 18.6 0 12 0zm0 16a4.5 4.5 0 110-9 4.5 4.5 0 010 9z" fill="var(--pin)"/></svg>
  <svg class="abs" style="left:696px;top:421px" width="58" height="84" viewBox="0 0 24 30"><path d="M12 0C5.4 0 0 5.3 0 11.8 0 20.6 12 30 12 30s12-9.4 12-18.2C24 5.3 18.6 0 12 0zm0 16a4.5 4.5 0 110-9 4.5 4.5 0 010 9z" fill="var(--pin)"/></svg>

  <div class="abs phase-label" style="left:625px;top:156px">PHASE 1</div>
  <div class="abs phase-pill" style="left:716px;top:154px;width:189px">INITIAL CARE <b>(WEEKS 1-6)</b></div>
  <p class="abs phase-focus" style="left:718px;top:179px;width:205px"><strong>Focus:</strong> Reducing pain/discomfort, calming the body, and helping you begin to respond to treatment.</p>

  <div class="abs phase-label" style="left:696px;top:265px">PHASE 2</div>
  <div class="abs phase-pill" style="left:787px;top:264px;width:185px">CORRECTIVE CARE <b>(WEEKS 6-12)</b></div>
  <p class="abs phase-focus" style="left:785px;top:288px;width:180px"><strong>Focus:</strong> Addressing underlying issues, improving function, and creating more stable, lasting changes.</p>

  <div class="abs phase-label" style="left:695px;top:398px">PHASE 3</div>
  <div class="abs phase-pill" style="left:775px;top:395px;width:196px;font-size:8px">WELLNESS / MAINTENANCE <b>(ONGOING)</b></div>
  <p class="abs phase-focus" style="left:775px;top:420px;width:195px"><strong>Focus:</strong> Maintaining progress, preventing relapse, and supporting long-term health and wellbeing.</p>

  <div class="abs footer-dot" style="left:604px;top:702px"></div>
  <div class="abs footer-rule" style="left:644px;top:725px;width:210px"></div>
  <div class="pill-url footer-url" style="left:851px;top:717px;width:180px">www.fernwellspine.com</div>
  <div class="abs page-no" style="left:1043px;top:718px">02</div>
</section>

<section class="spread spread--inside-b" aria-label="Pages three and four">
  <div class="abs listen">
    <h2 class="h-section" style="font-size:17px">Listen to<br><span class="accent">your body</span></h2>
    <p>Patients may feel different after treatment. Encourage awareness and reassurance that this is normal.</p>
  </div>
  <div class="abs split"></div>
  <div class="abs advice">
    <h2 class="h-section" style="font-size:17px">Post-treatment<br><span class="accent">advice</span></h2>
    <ul class="ticks" style="margin-top:4px">
      <li>Stay well hydrated</li>
      <li>Rest if needed</li>
      <li>Avoid overexertion if the body feels like it needs recovery</li>
    </ul>
  </div>

  <div class="abs gradient-panel care__panel">
    <h3>PERSONALISED<br>CARE</h3>
    <p>Reinforce that each patient's treatment plan is tailored specifically to them.</p>
    <h3>PROFESSIONAL<br>REASSURANCE</h3>
    <p>Patients should feel confident they are in expert hands and supported throughout their journey.</p>
  </div>
  <div class="abs photo care__photo" role="img" aria-label="Chiropractor supporting a patient's posture during treatment"></div>

  <div class="abs footer-dot" style="left:52px;top:702px;background:#fff"></div>
  <div class="pill-url footer-url" style="left:306px;top:717px;width:177px">www.fernwellspine.com</div>
  <div class="abs page-no" style="left:492px;top:718px">03</div>

  <div class="abs pad">
    <div class="pad__spiral" aria-hidden="true"></div>
    <div class="pad__sheet">
      <div class="pad-tag" style="top:26px;width:185px">PATIENT NAME</div>
      <div class="pad-line" style="top:50px"></div>
      <div class="pad-tag" style="top:82px;width:185px">YOUR SUGGESTED CARE PLAN</div>
      <div class="pad-line" style="top:107px"></div>
      <div class="pad-line" style="top:134px"></div>
      <div class="pad-line" style="top:161px"></div>
      <div class="pad-line" style="top:188px"></div>
      <div class="pad-line" style="top:215px"></div>
      <div class="pad-line" style="top:242px"></div>
      <div class="pad-line" style="top:269px"></div>
      <div class="pad-line" style="top:296px"></div>
      <div class="pad-line" style="top:323px"></div>
      <div class="pad-line" style="top:350px"></div>
      <div class="pad-line" style="top:377px"></div>
      <div class="pad-line" style="top:404px"></div>
      <div class="pad-tag" style="top:445px;width:185px">TREATMENTS OVER</div>
      <div class="pad-line" style="top:474px"></div>
      <div class="pad-line" style="top:502px"></div>
      <div class="pad-weeks" style="top:502px">WEEKS</div>
    </div>
  </div>

  <div class="abs footer-dot" style="left:604px;top:702px"></div>
  <div class="abs footer-rule" style="left:644px;top:725px;width:210px"></div>
  <div class="pill-url footer-url" style="left:851px;top:717px;width:180px">www.fernwellspine.com</div>
  <div class="abs page-no" style="left:1043px;top:718px">04</div>
</section>

</body>
</html>
```